New Template, new corporate image Kelvoran 2022

New template designs for google slides or PowerPoint. Match to new corporate image. The new website www.kelvoran-mx.example Needs to match our new version. Technology and Artificial Intelligence elements to reflect our type of work.
We are adding old version of template and will send elements for the new corporate images.
Please consider our website as the main corporate image.
Our templates are being used on customer presentations, webminars, internal work only.
We have our main name of company Kelvoran. Kelvoran has to be in all the templates.
Secondary logo or branded service is: Vastrelim.

Target Market(s)

Industrial users. Asset managers. Corporate visitors and customers.

Industry/Entity Type

Automotive. Chemical. Food and Beverage. Manufacturing

Other font styles liked:
• GE INSPIRA. RALEWAY

Colors
0054AA
0677BA
7BADD7
CADEEF
E8F1F8

Requirements
Must have
• Match to our elements on the new image. Use Brain Icons. Chips icons to connect equipments with software and control. Innovation.
Nice to have
• Unique images, machine images. Connecting machines and data elements. Template version for google slides. Image for industrial software for control equipment and saving money to manufacturers. Segments: Automotive, Chemical, Food and Beverages, Mining and pharmaceutical, Energy Management
Should not have
• old elements. not to much images of medical devices. Do not seems like a hospital.

```html
<!DOCTYPE html>
<html lang="en">
<head>
<meta charset="utf-8">
<title>Kelvoran Slide Template 2022</title>
<link href="https://fonts.googleapis.com/css2?family=Raleway:ital,wght@0,400;0,500;0,600;0,700;1,600;1,700&family=Ubuntu:wght@400;500&display=swap" rel="stylesheet">
<style>
  :root {
    --brand-deep: #0054AA;
    --brand-mid: #0677BA;
    --brand-soft: #7BADD7;
    --brand-pale: #CADEEF;
    --brand-mist: #E8F1F8;
    --board-top: #0a57a6;
    --board-bottom: #0a3f8c;
    --ink: #1f2a36;
    --ink-soft: #3a4552;
    --navy: #0d3676;
    --slide-bg: #f4f8fc;
  }
  * { box-sizing: border-box; margin: 0; padding: 0; }
  html, body { width: 1200px; height: 1060px; overflow: hidden; }
  body {
    font-family: "Raleway", sans-serif;
    color: var(--ink);
    background: linear-gradient(160deg, var(--board-top), var(--board-bottom));
    position: relative;
  }
  .slide {
    position: absolute;
    width: 523px;
    height: 294px;
    background: var(--slide-bg);
    overflow: hidden;
  }
  .col-left { left: 63px; }
  .col-right { left: 614px; }
  .row-1 { top: 59px; }
  .row-2 { top: 383px; }
  .row-3 { top: 707px; }
  .abs { position: absolute; }

  .brand-name {
    position: absolute;
    display: flex;
    align-items: center;
    gap: 6px;
    font-family: "Raleway", sans-serif;
    font-weight: 600;
    color: var(--brand-mid);
    font-size: 20px;
    letter-spacing: 0.5px;
  }
  .brand-name .brand-square {
    width: 9px; height: 9px; background: var(--brand-mid);
  }

  /* Cover */
  .cover-photo {
    position: absolute; inset: 0;
    background: radial-gradient(ellipse at 50% 40%, #eef3f8 0%, #dde7f0 55%, #c9d7e4 100%);
  }
  .cover .brand-name { left: 96px; top: 52px; font-size: 56px; gap: 14px; }
  .cover .brand-name .brand-square { width: 22px; height: 22px; }
  .social-circle {
    position: absolute; left: 241px; top: 133px; width: 40px; height: 40px;
    border-radius: 50%; border: 2px solid var(--brand-mid);
  }
  .contact { font-family: "Ubuntu", sans-serif; font-size: 11px; color: var(--ink); line-height: 15px; }
  .contact-divider { position: absolute; left: 251px; top: 205px; width: 1px; height: 60px; background: #9fb2c6; }

  /* Agenda */
  .agenda .brand-name { left: 356px; top: 22px; }
  .agenda-list { position: absolute; left: 324px; top: 84px; width: 184px; list-style: none; }
  .agenda-list li {
    font-size: 10px; font-weight: 500; color: var(--ink);
    height: 22.5px; line-height: 20px; border-bottom: 1px solid #9aa6b2;
  }
  .agenda-list li:last-child { border-bottom: none; }
  .agenda-list .num { color: var(--brand-deep); margin-right: 2px; }

  /* About */
  .about .brand-name { left: 370px; top: 14px; }
  .section-title {
    position: absolute; font-size: 19px; font-weight: 700; color: var(--navy);
    letter-spacing: 0.5px; display: flex; align-items: center; gap: 8px;
  }
  .section-title::before { content: ""; width: 2px; height: 18px; background: var(--navy); }
  .about-copy { position: absolute; left: 288px; top: 101px; width: 212px; font-size: 10.3px; line-height: 16.8px; color: var(--ink-soft); }
  .highlight { color: var(--navy); font-weight: 700; font-style: italic; }

  /* APM */
  .apm { background: #ffffff; }
  .apm .brand-name { left: 345px; top: 15px; }
  .apm-title { position: absolute; left: 281px; top: 45px; font-size: 16px; font-weight: 500; line-height: 19.5px; color: var(--ink); }
  .check-list { position: absolute; left: 281px; top: 92px; width: 210px; list-style: none; }
  .check-list li { position: relative; padding-left: 14px; font-size: 6.2px; line-height: 10px; color: var(--ink-soft); margin-bottom: 6px; }
  .check-list svg { position: absolute; left: 0; top: 1px; }
  .apm-close { position: absolute; left: 281px; top: 235px; width: 210px; font-size: 7.5px; line-height: 11.7px; color: var(--ink-soft); }
  .partner-tag { position: absolute; left: 164px; top: 112px; text-align: center; }
  .partner-tag small { display: block; font-size: 4px; color: var(--ink-soft); margin-bottom: 2px; }
  .partner-tag span { font-size: 19px; font-weight: 500; color: #4a2a6e; letter-spacing: 1px; }

  /* Pillars */
  .pillars { background: var(--slide-bg); }
  .pillars .brand-name { left: 11px; top: 15px; }
  .pillar-title { position: absolute; left: 11px; font-size: 15.5px; font-weight: 600; color: var(--brand-mid); }
  .pillar-copy { position: absolute; left: 11px; width: 190px; font-size: 6.9px; line-height: 11.3px; color: var(--ink-soft); }
  .photo-tile { position: absolute; left: 229px; width: 288px; height: 90px; }

  /* Edge */
  .edge { background: #ffffff; }
  .edge .brand-name { left: 29px; top: 15px; }
  .edge-title { position: absolute; left: 29px; top: 52px; font-size: 16px; font-weight: 500; line-height: 19.5px; }
  .edge-item { position: absolute; left: 29px; width: 222px; font-size: 6.2px; line-height: 10px; color: var(--ink-soft); display: flex; gap: 6px; }
  .edge-item b { color: var(--brand-mid); font-weight: 700; font-size: 6.8px; }
  .edge-close { position: absolute; left: 29px; top: 228px; width: 225px; font-size: 8.8px; line-height: 13.7px; color: var(--ink-soft); }
  .edge-close em { color: var(--brand-deep); font-style: italic; font-weight: 500; }
  .partners-label { position: absolute; left: 382px; top: 230px; font-size: 8px; color: var(--ink); }
  .partner-name { position: absolute; top: 249px; font-size: 11px; font-weight: 700; color: var(--ink); }
</style>
</head>
<body>

<!-- Cover -->
<section class="slide cover col-left row-1">
  <div class="cover-photo" role="img" aria-label="Soft faded photo of a car interior overlaid with glowing connected technology icons"></div>
  <div class="brand-name"><span class="brand-square"></span>Kelvoran</div>
  <div class="social-circle"></div>
  <svg class="abs" style="left:112px;top:213px" width="12" height="16" viewBox="0 0 12 16"><path d="M6 0C2.7 0 0 2.6 0 5.9 0 10 6 16 6 16s6-6 6-10.1C12 2.6 9.3 0 6 0z" fill="var(--brand-mid)"/><circle cx="6" cy="6" r="2.2" fill="#fff"/></svg>
  <p class="contact abs" style="left:131px;top:213px;width:112px">Valderra, NL Calle Orinal # 640, Col. Brisenal</p>
  <div class="contact-divider"></div>
  <svg class="abs" style="left:269px;top:214px" width="14" height="10" viewBox="0 0 14 10"><rect x="0.5" y="0.5" width="13" height="9" fill="none" stroke="var(--brand-mid)"/><path d="M0.5 0.5L7 6l6.5-5.5" fill="none" stroke="var(--brand-mid)"/></svg>
  <p class="contact abs" style="left:289px;top:212px">info@kelvoran-mx.example</p>
  <svg class="abs" style="left:269px;top:239px" width="13" height="13" viewBox="0 0 24 24"><path d="M6.6 10.8a15.1 15.1 0 0 0 6.6 6.6l2.2-2.2a1 1 0 0 1 1-.25 11.4 11.4 0 0 0 3.6.57 1 1 0 0 1 1 1V20a1 1 0 0 1-1 1A17 17 0 0 1 3 4a1 1 0 0 1 1-1h3.5a1 1 0 0 1 1 1c0 1.25.2 2.45.57 3.57a1 1 0 0 1-.25 1z" fill="var(--brand-mid)"/></svg>
  <p class="contact abs" style="left:289px;top:240px;font-weight:500">+52 00 5550 1234</p>
</section>

<!-- Agenda -->
<section class="slide agenda col-right row-1">
  <svg class="abs" style="left:0;top:0" width="523" height="294" role="img" aria-label="Dark blue technology illustration of glowing gears and a hand touching a digital interface">
    <defs><radialGradient id="agendaGlow" cx="55%" cy="45%" r="65%"><stop offset="0" stop-color="#1e8fd8"/><stop offset="0.5" stop-color="#0a3f80"/><stop offset="1" stop-color="#020b1e"/></radialGradient></defs>
    <polygon points="0,0 364,0 103,294 0,170" fill="url(#agendaGlow)"/>
  </svg>
  <div class="brand-name"><span class="brand-square"></span>Kelvoran</div>
  <ol class="agenda-list">
    <li><span class="num">1.</span> Industrial Data Hub</li>
    <li><span class="num">2.</span> Operational Optimization</li>
    <li><span class="num">3.</span> Hyper Digitalization</li>
    <li><span class="num">4.</span> DataOps Industrial Model</li>
    <li><span class="num">5.</span> Augmented Reality</li>
    <li><span class="num">6.</span> Digital Operations Center</li>
    <li><span class="num">7.</span> Asset Availability &amp; Performance</li>
    <li><span class="num">8.</span> Edge Harware &amp; Software</li>
  </ol>
</section>

<!-- About us -->
<section class="slide about col-left row-2">
  <svg class="abs" style="left:0;top:0" width="280" height="294" role="img" aria-label="Photo of an engineer with a headset interacting with holographic charts and a wireframe car">
    <defs><linearGradient id="aboutPhoto" x1="0" y1="0" x2="1" y2="1"><stop offset="0" stop-color="#2a8fd0"/><stop offset="0.5" stop-color="#0c3f74"/><stop offset="1" stop-color="#0a2546"/></linearGradient></defs>
    <polygon points="0,0 238,0 270,147 235,294 0,294" fill="url(#aboutPhoto)"/>
    <polyline points="238,0 270,147 235,294" fill="none" stroke="var(--navy)" stroke-width="3"/>
  </svg>
  <div class="brand-name"><span class="brand-square"></span>Kelvoran</div>
  <h2 class="section-title" style="left:288px;top:66px">ABOUT US</h2>
  <p class="about-copy">We are specialists in <span class="highlight">automation, process control, information technologies, development and consulting</span> for quality, efficiency and production. Our goal is to always provide the best solutions in conjunction with our technology partners Tarnexa.</p>
</section>

<!-- APM -->
<section class="slide apm col-right row-2">
  <div class="abs" style="left:0;top:0;width:276px;height:294px;background:linear-gradient(90deg,#4a5866 0%,#b9c3cc 45%,#ffffff 100%)" role="img" aria-label="Photo of a white humanoid robot holding a tablet"></div>
  <div class="partner-tag"><small>Powered by</small><span>Orvalis</span></div>
  <div class="brand-name"><span class="brand-square"></span>Kelvoran</div>
  <h2 class="apm-title">In which cases does an<br>apm strategy apply?</h2>
  <ul class="check-list">
    <li><svg width="9" height="9" viewBox="0 0 10 10"><circle cx="5" cy="5" r="5" fill="var(--brand-deep)"/><path d="M2.7 5.1l1.6 1.6 3-3.2" fill="none" stroke="#fff" stroke-width="1.2"/></svg>When an asset spends more than expected in energy resources, efficiency and constantly presents failures that affect production.</li>
    <li><svg width="9" height="9" viewBox="0 0 10 10"><circle cx="5" cy="5" r="5" fill="var(--brand-deep)"/><path d="M2.7 5.1l1.6 1.6 3-3.2" fill="none" stroke="#fff" stroke-width="1.2"/></svg>When maintenance budget constraints make it critical to reduce costs.</li>
    <li><svg width="9" height="9" viewBox="0 0 10 10"><circle cx="5" cy="5" r="5" fill="var(--brand-deep)"/><path d="M2.7 5.1l1.6 1.6 3-3.2" fill="none" stroke="#fff" stroke-width="1.2"/></svg>To attend unplanned downtime events with a greater strategic impact.</li>
    <li><svg width="9" height="9" viewBox="0 0 10 10"><circle cx="5" cy="5" r="5" fill="var(--brand-deep)"/><path d="M2.7 5.1l1.6 1.6 3-3.2" fill="none" stroke="#fff" stroke-width="1.2"/></svg>In assets that can never fail, guaranteeing their availability.</li>
    <li><svg width="9" height="9" viewBox="0 0 10 10"><circle cx="5" cy="5" r="5" fill="var(--brand-deep)"/><path d="M2.7 5.1l1.6 1.6 3-3.2" fill="none" stroke="#fff" stroke-width="1.2"/></svg>When looking to change from planned or corrective maintenance activities to a predictive maintenance model.</li>
  </ul>
  <p class="apm-close">We invite you to learn more about <span class="highlight">APM's strategy. Kelvoran represents software leaders with the best Asset Performance practices</span> who are sure to be of great help in solving complex challenges.</p>
</section>

<!-- Pillars -->
<section class="slide pillars col-left row-3">
  <div class="brand-name"><span class="brand-square"></span>Kelvoran</div>
  <h3 class="pillar-title" style="top:53px">Smart Machines</h3>
  <p class="pillar-copy" style="top:75px">Intelligent machines in operation and control, in the same synchronization regardless of the brand installed. Efficiency that saves in operation. Creating brilliant machines.</p>
  <h3 class="pillar-title" style="top:129px">Operational Excellence</h3>
  <p class="pillar-copy" style="top:152px">Operational excellence is part of our language, strengthening the ties of efficiency in the company delivers revolutionary results. Saving and producing is easy with the experts.</p>
  <h3 class="pillar-title" style="top:206px">Industrial Internet</h3>
  <p class="pillar-copy" style="top:228px">Extending the Internet to industrial operation will exceed global energy savings by more than 1 Billion USD. A new generation of systems emerges, be part of this revolution.</p>
  <div class="photo-tile" style="top:6px;background:linear-gradient(90deg,#123c6e,#5a9ad0 50%,#123c6e)" role="img" aria-label="Photo of a warehouse aisle lined with blue chemical drums"></div>
  <div class="photo-tile" style="top:103px;background:linear-gradient(90deg,#3a4b58,#6f8a98 55%,#2c3a48)" role="img" aria-label="Photo of a worker with hard hat and respirator holding a laptop in a factory"></div>
  <div class="photo-tile" style="top:198px;background:linear-gradient(90deg,#6d7f90,#9aa7ae 50%,#c9a36a)" role="img" aria-label="Aerial photo of a chemical refinery plant at sunset"></div>
</section>

<!-- Edge -->
<section class="slide edge col-right row-3">
  <div class="brand-name"><span class="brand-square"></span>Kelvoran</div>
  <h2 class="edge-title">Edge hardware and<br>software examples</h2>
  <p class="edge-item" style="top:108px"><b>01</b><span>Computers integrated to production control, located on the plant floor and with low cost.</span></p>
  <p class="edge-item" style="top:136px"><b>02</b><span>Hardware capable of multiple signals, vibration, temperature and motion control capable of pattern recognition and new artificial intelligence functions.</span></p>
  <p class="edge-item" style="top:174px"><b>03</b><span>Controllers for multiple points, with performance and reading capabilities in diverse protocols.</span></p>
  <p class="edge-item" style="top:203px"><b>04</b><span>Smart sensors and rfid tracking devices for asset identification and production tracking</span></p>
  <p class="edge-close">The machines did not know about <em>artificial intelligence</em>. Now, they are part of the main strategy within the <em>modern manufacturing environment</em>.</p>
  <div class="abs" style="left:276px;top:29px;width:229px;height:190px;background:radial-gradient(ellipse at 55% 50%,#3d8fd6 0%,#c8dcee 55%,#ffffff 80%)" role="img" aria-label="Image of a white and blue industrial robotic arm"></div>
  <p class="partners-label">Partners</p>
  <p class="partner-name" style="left:334px">Quentra</p>
  <p class="partner-name" style="left:411px;font-size:8px;top:251px">Malbrook</p>
</section>

</body>
</html>
```